Redesign Of Current Landing Page

I need to redesign this landing page https://www.brightlanepromo.biz/?page=landing&landing=23 (Please do not opt in because when you do it will show you the home page. Please clear your cookies before going to this url above to view the 1 page landing page.)

Please use my updated website as a reference for colors and logo.
http://sitecradlewerk.com/dh/bpq/index.html

I would like the call to action to be a button that opens into a lead form...

Button would be "Download Samples"

Target Market(s)

small business owners

Industry/Entity Type

Marketing

Number of Pages Required

1 page

Colors

Designer to choose colors to be used in the design.

Requirements
Must have
• must be full responsive on all devices
Nice to have
• must have a legitimate professional apeal to it
Should not have
• open

```html
<!DOCTYPE html>
<html lang="en">
<head>
<meta charset="utf-8">
<title>BLPG – Brightlane Promo Incentives</title>
<link href="https://fonts.googleapis.com/css2?family=Roboto:wght@300;400;500;700&family=Open+Sans:wght@400;600&display=swap" rel="stylesheet">
<style>
:root{
  --blue:#0a6ccb;
  --blue-dark:#0756a5;
  --navy:#1d2b3a;
  --ink:#333;
  --muted:#666;
  --light:#f4f6f9;
  --footer:#eef0f3;
  --grey-btn:#6b6b6b;
  --white:#fff;
}
*{box-sizing:border-box;margin:0;padding:0}
html,body{width:1200px;height:2195px;overflow:hidden}
body{position:relative;font-family:"Open Sans",Arial,sans-serif;color:var(--ink);background:var(--white)}
.abs{position:absolute}
.roboto{font-family:"Roboto",Arial,sans-serif}

/* header */
.site-header{left:0;top:0;width:1200px;height:88px;background:var(--white)}
.brand{left:85px;top:20px;display:flex;align-items:center;gap:10px}
.brand-dot{width:36px;height:36px;border-radius:50%;background:var(--blue)}
.brand-name{font-family:"Roboto",sans-serif;font-weight:700;font-size:32px;color:var(--navy);letter-spacing:1px}
.account-tabs{left:875px;top:0;height:32px;width:237px;display:flex;font-family:"Roboto",sans-serif;font-size:12px;color:#fff}
.account-tabs span{display:flex;align-items:center;justify-content:center;gap:6px;flex:1}
.tab-login{background:#3b4450;border-radius:0 0 0 18px}
.tab-signup{background:var(--blue);border-radius:0 0 18px 0}
.main-nav{top:53px;right:88px;display:flex;gap:45px;font-family:"Roboto",sans-serif;font-size:12px;color:#333}
.main-nav .active{color:var(--blue)}

/* hero */
.hero{left:0;top:88px;width:1200px;height:508px;background:linear-gradient(100deg,#f3f4f7 0%,#e7ecf2 35%,#b9c7d6 60%,#6f88a3 85%,#4d6a88 100%)}
.hero-title{left:86px;top:188px;font-family:"Roboto",sans-serif;font-weight:500;font-size:41px;color:var(--blue);letter-spacing:.5px}
.hero-sub{left:86px;top:246px;font-family:"Roboto",sans-serif;font-weight:300;font-size:32px;color:#555;letter-spacing:.5px}
.hero-text{left:86px;top:302px;width:400px;font-size:12px;line-height:28px;color:#555}
.btn-outline{display:flex;align-items:center;justify-content:center;border:2px solid var(--blue);color:var(--blue);font-family:"Roboto",sans-serif;font-weight:500;background:rgba(255,255,255,.4)}
.hero-btn{left:86px;top:404px;width:186px;height:48px;font-size:15px}

/* features */
.features{left:0;top:596px;width:1200px;height:175px;background:#eef0f3}
.feature{width:190px;text-align:center;top:537px}
.feature .disc{width:132px;height:132px;margin:0 auto;border-radius:50%;background:var(--blue);border:5px solid #fff;display:flex;align-items:center;justify-content:center;box-shadow:0 2px 6px rgba(0,0,0,.1)}
.feature p{margin-top:14px;font-family:"Roboto",sans-serif;font-size:11.5px;line-height:23px;color:#333;text-transform:uppercase}

/* welcome */
.welcome{left:0;top:771px;width:1200px;height:290px;background:#fff;text-align:center}
.welcome h2{position:absolute;top:34px;width:100%;font-family:"Roboto",sans-serif;font-weight:300;font-size:25px;color:var(--blue)}
.welcome p{position:absolute;left:225px;top:82px;width:750px;font-size:12px;line-height:27px;color:#555}
.btn-solid{display:flex;align-items:center;justify-content:center;color:#fff;font-family:"Roboto",sans-serif;font-weight:500;font-size:14px}

/* columns */
.columns{left:0;top:1061px;width:1200px;height:490px;background:var(--light)}
.col{top:1106px;width:328px}
.col h3{font-family:"Roboto",sans-serif;font-weight:500;font-size:17px;color:#333;height:30px}
.col .photo{margin-top:12px;width:328px;height:208px;border:4px solid #fff;box-shadow:0 0 0 1px #ddd}
.col p{margin-top:18px;font-size:11.5px;line-height:26px;color:#555}
.col .btn-outline{margin-top:22px;width:118px;height:38px;font-size:13px;background:#fff}

/* about & testimonials */
.about-title,.testi-title{font-family:"Roboto",sans-serif;font-weight:300;font-size:25px;color:var(--blue);top:1586px}
.about-text{left:86px;top:1637px;width:380px;font-size:11.5px;line-height:23px;color:#555}
.testi-photo{left:518px;top:1642px;width:126px;height:126px;border-radius:50%;background:radial-gradient(circle at 50% 40%,#d9b39a,#7a5240)}
.testi-quote{left:683px;top:1668px;width:430px;font-size:11.5px;line-height:23.5px;color:#555}
.quote-mark{font-family:Georgia,serif;font-size:28px;color:#888}
.testi-name{left:683px;top:1786px;font-size:13px;color:#888}
.testi-name b{color:var(--blue);font-weight:600}

/* footer */
.footer{left:0;top:1883px;width:1200px;height:243px;background:var(--footer)}
.foot-brand{left:116px;top:1980px;display:flex;align-items:center;gap:10px}
.foot-brand .brand-dot{width:44px;height:44px}
.foot-brand .brand-name{font-size:38px}
.foot-h{font-family:"Roboto",sans-serif;font-size:15px;color:#333;top:1914px;letter-spacing:.3px}
.contact-list{left:378px;top:1957px;font-size:11.5px;color:#666;list-style:none}
.contact-list li{display:flex;gap:12px;align-items:flex-start;height:29px}
.contact-list li:last-child{line-height:15px}
.contact-list u{color:#666}
.news-text{left:625px;top:1956px;width:230px;font-size:11.5px;line-height:20px;color:#777}
.email-field{left:625px;top:2015px;width:212px;height:31px;border:1px solid #ccc;background:#fff;font-size:12px;color:#555;padding:8px 14px}
.subscribe{left:625px;top:2052px;width:80px;height:29px;background:var(--blue);color:#fff;font-size:10px;font-weight:600;display:flex;align-items:center;justify-content:center}
.follow-text{left:885px;top:1958px;width:200px;font-size:10.5px;line-height:20px;color:#888}
.social{top:2034px;width:36px;height:36px;border-radius:50%;border:2px solid #aaa}
.copyright{left:0;top:2126px;width:1200px;height:69px;background:var(--blue);color:#fff;font-size:12px;display:flex;align-items:center;justify-content:center}
</style>
</head>
<body>

<header class="site-header abs">
  <div class="brand abs"><span class="brand-dot"></span><span class="brand-name">BLPG</span></div>
  <div class="account-tabs abs">
    <span class="tab-login"><svg width="10" height="11" viewBox="0 0 10 11"><rect x="1" y="5" width="8" height="6" fill="#fff"/><path d="M3 5V3a2 2 0 014 0v2" stroke="#fff" fill="none" stroke-width="1.5"/></svg>LOGIN</span>
    <span class="tab-signup"><svg width="11" height="10" viewBox="0 0 11 10"><path d="M0 5h6M4 2l3 3-3 3" stroke="#fff" stroke-width="1.6" fill="none"/><path d="M7 1h3v8H7" stroke="#fff" stroke-width="1.4" fill="none"/></svg>SIGN UP</span>
  </div>
  <nav class="main-nav abs">
    <span class="active">HOME</span><span>ABOUT US</span><span>SERVICES</span><span>PRODUCTS</span><span>NEWS</span><span>CONTACT US</span>
  </nav>
</header>

<section class="hero abs" role="img" aria-label="Photo of hands working over a laptop and sales charts with overlaid data graphics"></section>
<h1 class="hero-title abs">BRIGHTLANE</h1>
<div class="hero-sub abs">PROMO INCENTIVES</div>
<p class="hero-text abs">We help fill empty rooms for thousands of hotels and resorts in hund reds of destinations around the world as well as the major cruise lines. Hotels and resorts are rarely</p>
<div class="btn-outline hero-btn abs">DOWNLOAD SAMPLE</div>

<section class="features abs"></section>
<div class="feature abs" style="left:63px">
  <div class="disc"><svg width="60" height="50" viewBox="0 0 60 50" fill="#fff"><rect x="4" y="30" width="7" height="16"/><rect x="15" y="24" width="7" height="22"/><rect x="26" y="26" width="7" height="20"/><rect x="37" y="18" width="7" height="28"/><rect x="48" y="12" width="7" height="34"/><path d="M6 22l12-8 10 4 18-12" stroke="#fff" stroke-width="3" fill="none"/></svg></div>
  <p>Increase responses<br>from your existing ads</p>
</div>
<div class="feature abs" style="left:240px">
  <div class="disc"><svg width="56" height="56" viewBox="0 0 56 56" stroke="#fff" stroke-width="6" stroke-linecap="round"><path d="M12 12l32 32"/><path d="M44 12L12 44"/><circle cx="44" cy="12" r="6" fill="none" stroke-width="4"/></svg></div>
  <p>#1 sales closing tool -<br>gift w/ purchase</p>
</div>
<div class="feature abs" style="left:416px">
  <div class="disc"><svg width="56" height="56" viewBox="0 0 56 56"><path d="M28 5l7 15 16 2-12 11 3 16-14-8-14 8 3-16L5 22l16-2z" fill="none" stroke="#fff" stroke-width="4" stroke-linejoin="round"/></svg></div>
  <p>Build brand awareness<br>and trust</p>
</div>
<div class="feature abs" style="left:591px">
  <div class="disc"><svg width="64" height="48" viewBox="0 0 64 48" fill="#fff"><circle cx="32" cy="13" r="9"/><path d="M16 46c0-12 7-20 16-20s16 8 16 20z"/><circle cx="13" cy="17" r="7"/><path d="M0 42c0-9 5-14 13-14 3 0 5 1 6 2-3 4-5 8-5 12z"/><circle cx="51" cy="17" r="7"/><path d="M64 42c0-9-5-14-13-14-3 0-5 1-6 2 3 4 5 8 5 12z"/></svg></div>
  <p>Insure the sale over<br>your competition</p>
</div>
<div class="feature abs" style="left:767px">
  <div class="disc"><svg width="52" height="56" viewBox="0 0 52 56" fill="#fff"><path d="M8 30C8 16 18 8 32 9V2l14 12-14 12v-8c-9 0-15 5-16 14z"/><path d="M44 26c0 14-10 22-24 21v7L6 42l14-12v8c9 0 15-5 16-14z"/></svg></div>
  <p>Boost repeat and<br>referral business-</p>
</div>
<div class="feature abs" style="left:943px">
  <div class="disc"><svg width="58" height="58" viewBox="0 0 58 58" fill="none" stroke="#fff" stroke-width="4"><path d="M48 22A20 20 0 1 0 48 38"/><path d="M42 20l7 2 2-7"/><text x="29" y="38" font-family="Roboto,sans-serif" font-size="26" font-weight="700" fill="#fff" stroke="none" text-anchor="middle">$</text></svg></div>
  <p>Improve retention<br>rates</p>
</div>

<section class="welcome abs">
  <h2>WELCOME TO OUR COMPANY</h2>
  <p>We help fill empty rooms for thousands of hotels and resorts in hundreds of destinations around the world as well as the major cruise lines. Hotels and resorts are rarely full so when we place someone in their empty rooms, they end up making it up when travelers spend money on room service, spa services, eat at their in-house restaurants, casino</p>
  <div class="btn-solid abs" style="left:458px;top:192px;width:132px;height:44px;background:var(--grey-btn)">READ MORE</div>
  <div class="btn-solid abs" style="left:600px;top:192px;width:142px;height:44px;background:var(--blue)">OUR FEATURED</div>
</section>

<section class="columns abs"></section>
<article class="col abs" style="left:85px">
  <h3>CREATIVE MARKETING</h3>
  <div class="photo" role="img" aria-label="Hand writing marketing keywords on a dark blue board" style="background:linear-gradient(135deg,#0d1f4d,#1c3c8a 60%,#c8c8d8)"></div>
  <p>Hotels and resorts are rarely full so when we place someone in their empty rooms, they end up making it up when travelers spend money on room service, spa services</p>
  <div class="btn-outline">LEARN MORE</div>
</article>
<article class="col abs" style="left:435px">
  <h3>HOW IT WORKS</h3>
  <div class="photo" role="img" aria-label="Desk with a B2B marketing notebook, keyboard, coffee and sticky notes" style="background:linear-gradient(135deg,#e8e6e2,#cfcac2 50%,#6b6f6a)"></div>
  <p>Hotels and resorts are rarely full so when we place someone in their empty rooms, they end up making it up when travelers spend money on room service, spa services</p>
  <div class="btn-outline">LEARN MORE</div>
</article>
<article class="col abs" style="left:784px">
  <h3>HOW CAN WE DO IT</h3>
  <div class="photo" role="img" aria-label="Man working at a desktop computer in a bright office" style="background:linear-gradient(135deg,#3e3a36,#8a8279 50%,#d9dde2)"></div>
  <p>Hotels and resorts are rarely full so when we place someone in their empty rooms, they end up making it up when travelers spend money on room service, spa services</p>
  <div class="btn-outline">LEARN MORE</div>
</article>

<h2 class="about-title abs" style="left:88px">ABOUT US</h2>
<p class="about-text abs">being able to create exciting give away promotions that will boost your sales without ever having to worry about cost. Brightlane Promo Group, Inc. provides high-perceived value promotional incentives to businesses that want to advertise an exciting Give Away that will instantly attract more customers from your existing advertising business can give away incentive certificates efforts.</p>
<div class="btn-outline abs" style="left:86px;top:1801px;width:125px;height:39px;font-size:13px">READ MORE</div>

<h2 class="testi-title abs" style="left:520px">TESTIMONIALS</h2>
<div class="testi-photo abs" role="img" aria-label="Portrait photo of a smiling customer"></div>
<span class="quote-mark abs" style="left:664px;top:1652px">&ldquo;</span>
<p class="testi-quote abs">I began using your incentives two years ago to boost lead generation efforts. I have experienced a 63% increase in lead captures. And, even more importantly, my sales have increased as well. The ability to offer unlimited certificates and not having to pay for each certificate I give away is perhaps...</p>
<span class="quote-mark abs" style="left:990px;top:1742px">&rdquo;</span>
<p class="testi-name abs"><b>Dana R.</b> Ashford, TN</p>

<footer class="footer abs"></footer>
<div class="foot-brand abs"><span class="brand-dot"></span><span class="brand-name">BLPG</span></div>
<h4 class="foot-h abs" style="left:378px">CONTACT US</h4>
<ul class="contact-list abs">
  <li><svg width="12" height="12" viewBox="0 0 12 12" fill="#777"><rect x="1" y="4" width="10" height="7"/><path d="M0 4c2-3 10-3 12 0z"/></svg>(000)-121-1231 (Phone)</li>
  <li><svg width="12" height="12" viewBox="0 0 12 12" fill="#777"><rect x="3" y="0" width="6" height="4"/><rect x="0" y="4" width="12" height="5"/><rect x="3" y="8" width="6" height="4"/></svg>(000)-121-1231 (Fax)</li>
  <li><svg width="12" height="12" viewBox="0 0 12 12"><rect x="0.5" y="2.5" width="11" height="8" fill="#777"/><path d="M1 3l5 4 5-4" stroke="#fff" fill="none"/></svg><u>brightlanepromo.com</u></li>
  <li><svg width="12" height="14" viewBox="0 0 12 14" fill="#777"><path d="M6 0a5 5 0 015 5c0 4-5 9-5 9S1 9 1 5a5 5 0 015-5z"/><circle cx="6" cy="5" r="2" fill="#eef0f3"/></svg><span>70 Lorem Ipsum Dummy Lorem<br>Ipsum Dummy</span></li>
</ul>
<h4 class="foot-h abs" style="left:625px">NEWSLETTER</h4>
<p class="news-text abs">Register Your email address to get information ablout us</p>
<div class="email-field abs">Email Address</div>
<div class="subscribe abs">SUBSCRIBE</div>
<h4 class="foot-h abs" style="left:885px">FOLLOW US</h4>
<p class="follow-text abs">Lorem ipsum dolor sit amet, conse ctetur adipiscing elit. Nulla in purus nibh. Donec ornare</p>
<span class="social abs" style="left:882px"></span>
<span class="social abs" style="left:926px"></span>
<span class="social abs" style="left:968px"></span>
<span class="social abs" style="left:1011px"></span>
<span class="social abs" style="left:1055px"></span>
<div class="copyright abs">© Copyright 2017 Brightlane Promo Incentives.All Rights Reserved</div>

</body>
</html>
```